New Business Card Design Project

Need a design that will create an impact / strong impression towards our clients for our business. We are in the lighting business and we do lighting retrofits for large commercial to industrial clientele.

Target Market(s)

Lighting Industry

Industry/Entity Type

Business

Font styles to use
Other font styles liked:
• we would like to use the font on our logo, not sure what it is though..

Requirements
Must have
• Our logo.
Nice to have
• We are open to suggestions that have to do with lighting.

```html
<!DOCTYPE html>
<html lang="en">
<head>
<meta charset="utf-8">
<title>Brightline Retrofit Co. — Business Card</title>
<link rel="stylesheet" href="https://fonts.googleapis.com/css2?family=Lato:wght@400;700;900&display=swap">
<style>
  :root {
    --bg: #3a3a3c;
    --green-dark: #12380f;
    --green-mid: #0f8a3a;
    --green-light: #5cc15c;
    --white: #ffffff;
  }
  * { margin: 0; padding: 0; box-sizing: border-box; }
  html, body { width: 1200px; height: 900px; overflow: hidden; }
  body {
    background: var(--bg);
    font-family: "Lato", sans-serif;
    position: relative;
  }
  .card {
    position: absolute;
    left: 250px;
    width: 700px;
    height: 400px;
    overflow: hidden;
  }
  .card--back { top: 40px; background: var(--green-dark); }
  .card--front { top: 470px; background: var(--white); }

  .brand {
    position: absolute;
    display: flex;
    align-items: center;
    gap: 14px;
    font-weight: 900;
    letter-spacing: 1px;
  }
  .brand__mark { width: 22px; height: 22px; background: currentColor; }
  .card--back .brand {
    top: 130px; left: 0; width: 100%;
    justify-content: center;
    color: var(--white);
    font-size: 48px;
  }
  .card--back .website {
    position: absolute;
    top: 300px; left: 0; width: 100%;
    text-align: center;
    color: var(--white);
    font-size: 17px;
    letter-spacing: 1.5px;
  }

  .card--front .brand {
    top: 70px; left: 50px;
    color: var(--green-dark);
    font-size: 44px;
  }
  .front-art { position: absolute; inset: 0; }
  .address {
    position: absolute;
    left: 40px; top: 300px;
    color: var(--white);
    font-size: 21px;
    line-height: 1.3;
  }
  .contact {
    position: absolute;
    right: 40px; top: 220px;
    text-align: right;
    color: var(--white);
  }
  .contact__name { font-size: 27px; font-weight: 700; line-height: 1.2; }
  .contact__role { font-size: 19px; color: var(--green-mid); margin-bottom: 8px; line-height: 1.2; }
  .contact__list { list-style: none; font-size: 18px; line-height: 1.3; }
  .contact__list li { display: flex; justify-content: flex-end; align-items: center; gap: 12px; }
  .contact__list svg { width: 16px; height: 16px; fill: var(--green-mid); }
</style>
</head>
<body>

<section class="card card--back">
  <div class="brand"><span class="brand__mark"></span>Brightline Retrofit Co.</div>
  <p class="website">www.brightline-retrofit.com</p>
</section>

<section class="card card--front">
  <svg class="front-art" viewBox="0 0 700 400" aria-hidden="true">
    <path d="M0,250 Q220,295 420,240 Q590,190 700,10 V400 H0 Z" fill="var(--green-dark)"/>
    <path d="M330,258 Q560,210 640,0 L675,0 Q585,222 330,258 Z" fill="var(--green-mid)"/>
  </svg>

  <div class="brand"><span class="brand__mark"></span>Brightline Retrofit Co.</div>

  <p class="address">1480 Lakeview Avenue<br>Maple Grove, IL 60000</p>

  <div class="contact">
    <p class="contact__name">Marcus Hale</p>
    <p class="contact__role">Manager</p>
    <ul class="contact__list">
      <li>(555) 014-2290
        <svg viewBox="0 0 24 24"><path d="M6.6 10.8a15 15 0 0 0 6.6 6.6l2.2-2.2c.3-.3.7-.4 1-.2 1.1.4 2.3.6 3.6.6.6 0 1 .4 1 1V20c0 .6-.4 1-1 1A17 17 0 0 1 3 4c0-.6.4-1 1-1h3.5c.6 0 1 .4 1 1 0 1.3.2 2.5.6 3.6.1.3 0 .7-.2 1z"/></svg>
      </li>
      <li>(555) 014-2291
        <svg viewBox="0 0 24 24"><path d="M6 2h12v5H6zM4 8h16a2 2 0 0 1 2 2v7h-4v5H6v-5H2v-7a2 2 0 0 1 2-2zm4 8v4h8v-4z"/></svg>
      </li>
      <li>info@brightline-retrofit.com
        <svg viewBox="0 0 24 24"><path d="M2 5h20v14H2zm2 2v.5l8 5 8-5V7z"/></svg>
      </li>
      <li>www.brightline-retrofit.com
        <svg viewBox="0 0 24 24"><circle cx="12" cy="12" r="10"/></svg>
      </li>
    </ul>
  </div>
</section>

</body>
</html>
```